Printed magazine advertisement for a book about piano styles.

Hello all,

I need a design for an ad:

Goal: I am trying to promote my book about various national styles of playing classical piano.

1. Ad will be printed in several piano-related magazines, here are examples:

http://www.velmarsh.co.uk/velmarsh-press/journals/tessera-review/
http://www.bqlo.org/
https://www.corvettajournal.com/

2. I would like to ask for a design that can be adjusted to 3 size specifications so that I can post it in magazines (please see 'File specifications' attachment).

3. To save you time, please create a design in a single format. If successful, we can then adjust it to other specifications.

4. Here is my website this discusses the book: http://ostrandmeridian.com/

5. If possible, the design should include:
- QRS code
- Zentrovo logo (book is available through Zentrovo, please pick logo version suitable to your design)
- Book cover (it can include only the front page, up to your discretion)
- Blurb (see 'Ad blurb')

7. The character of the ad should be: classy, trustworthy, professional

Please let me know if there are any issues with fitting all the required text into the specified size. I can try to make it shorter.

Thank you for your interest.

Target Market(s)

Piano professionals, pianists, teachers, academic researchers

Requirements
Must have
• All must haves are already described in Project description.

```html
<!DOCTYPE html>
<html lang="en">
<head>
<meta charset="utf-8">
<title>Charting National Keyboard Styles – Advertisement</title>
<link rel="stylesheet" href="https://fonts.googleapis.com/css2?family=Cinzel:wght@700&family=Kaushan+Script&family=Roboto+Slab:wght@300;400;700&family=Arimo:wght@400;700&family=Tinos:wght@700&display=swap">
<style>
  :root {
    --page: #ffffff;
    --frame: #8a8a8a;
    --wood-light: #f1c896;
    --wood-mid: #e6b27c;
    --wood-dark: #d69d66;
    --ribbon: #f08a35;
    --ink: #3a2b22;
    --text: #2b2b2b;
    --quote-mark: #ee8a2e;
    --book-dark: #2f3236;
    --book-light: #8d9aa8;
    --badge-bg: #f4f4f4;
    --badge-edge: #9a9a9a;
  }
  * { box-sizing: border-box; margin: 0; padding: 0; }
  html, body { width: 1200px; height: 837px; overflow: hidden; background: var(--page); }
  .ad {
    position: absolute; left: 44px; top: 44px; width: 1113px; height: 748px;
    border: 1px solid var(--frame); overflow: hidden;
  }
  .ad__wood {
    position: absolute; inset: 0;
    background: linear-gradient(100deg, var(--wood-light) 0%, var(--wood-mid) 45%, var(--wood-light) 70%, var(--wood-dark) 100%);
  }
  .ribbon { position: absolute; left: 0; top: 68px; width: 612px; height: 166px; }
  .ribbon svg { position: absolute; inset: 0; }
  .ribbon__text {
    position: absolute; left: 0; top: 14px; width: 560px; text-align: center; color: var(--ink);
  }
  .ribbon__title {
    font-family: "Cinzel", serif; font-weight: 700; font-size: 40px; line-height: 46px; letter-spacing: 0.5px;
  }
  .ribbon__subtitle { font-family: "Kaushan Script", cursive; font-size: 37px; line-height: 48px; }
  .author {
    position: absolute; left: 100px; top: 257px; width: 460px; text-align: center;
    font-family: "Tinos", serif; font-weight: 700; font-size: 15px; color: var(--text);
  }
  .blurb {
    position: absolute; left: 96px; top: 286px; width: 468px; text-align: center;
    font-family: "Arimo", sans-serif; font-size: 15.3px; line-height: 24.5px; color: var(--text);
  }
  .quote__mark {
    position: absolute; font-family: "Roboto Slab", serif; font-weight: 700; font-size: 120px;
    line-height: 1; color: var(--quote-mark);
  }
  .quote__mark--open { left: 66px; top: 456px; }
  .quote__mark--close { left: 484px; top: 566px; }
  .quote__text {
    position: absolute; left: 128px; top: 494px; width: 412px; text-align: justify;
    font-family: "Roboto Slab", serif; font-weight: 300; font-size: 16.8px; line-height: 23.5px;
    letter-spacing: 0.3px; color: var(--text);
  }
  .site-link {
    position: absolute; left: 78px; top: 664px;
    font-family: "Arimo", sans-serif; font-size: 15px; color: var(--text);
  }
  .site-link strong { font-weight: 700; }
  .book { position: absolute; left: 616px; top: 98px; width: 360px; height: 556px; }
  .retail {
    position: absolute; left: 714px; top: 657px; width: 118px; height: 57px;
    background: var(--badge-bg); border: 1px solid var(--badge-edge); border-radius: 9px;
    text-align: center; font-family: "Arimo", sans-serif; color: #111;
  }
  .retail__label { display: block; font-size: 11px; line-height: 13px; margin-top: 6px; }
  .retail__name { display: block; font-size: 22px; line-height: 26px; font-weight: 700; }
  .pointer { position: absolute; left: 808px; top: 698px; width: 22px; height: 28px; }
</style>
</head>
<body>
<main class="ad">
  <div class="ad__wood" role="img" aria-label="Light wooden tabletop surface with soft grain"></div>

  <header class="ribbon">
    <svg width="612" height="166" viewBox="0 0 612 166" aria-hidden="true">
      <polygon points="0,0 612,0 560,83 612,166 0,166" fill="var(--ribbon)"/>
    </svg>
    <div class="ribbon__text">
      <h1 class="ribbon__title">CHARTING NATIONAL<br>KEYBOARD STYLES</h1>
      <p class="ribbon__subtitle">Traditions and tensions</p>
    </div>
  </header>

  <p class="author">Dr Radoslaw Wierzbicki</p>

  <p class="blurb">This volume grew out of a six-year research project into the idea of distinct national keyboard traditions. It traces how Russian, Central European, Italian and French styles of playing have developed and changed, and sets out the main lenses through which such traditions can be read (among them history, speech, touch, and shared culture)</p>

  <blockquote class="quote">
    <span class="quote__mark quote__mark--open" aria-hidden="true">“</span>
    <p class="quote__text">Pianists often trace their lineage back to, for example, Marenholt. But I think through changes in society, migration of the people, the whole change of attitude, I do not think there is anything left of that Marenholt tradition.</p>
    <span class="quote__mark quote__mark--close" aria-hidden="true">”</span>
  </blockquote>

  <p class="site-link">Read excerpts from the book: <strong>www.ostrandmeridian.com</strong></p>

  <svg class="book" viewBox="0 0 360 556" role="img" aria-label="Hardback book standing upright, dark grey cover with brushed silver bands carrying the title">
    <defs>
      <linearGradient id="coverTone" x1="0" y1="0" x2="1" y2="1">
        <stop offset="0" stop-color="var(--book-light)"/>
        <stop offset="0.35" stop-color="var(--book-dark)"/>
        <stop offset="1" stop-color="#25282c"/>
      </linearGradient>
      <radialGradient id="bookShadow" cx="0.5" cy="0.5" r="0.5">
        <stop offset="0" stop-color="#000" stop-opacity="0.35"/>
        <stop offset="1" stop-color="#000" stop-opacity="0"/>
      </radialGradient>
    </defs>
    <ellipse cx="180" cy="540" rx="190" ry="18" fill="url(#bookShadow)"/>
    <polygon points="6,20 348,0 354,544 6,520" fill="url(#coverTone)"/>
    <polygon points="348,0 356,4 360,540 354,544" fill="#dfe3e7"/>
  </svg>

  <div class="retail">
    <span class="retail__label">Available at</span>
    <span class="retail__name">Zentrovo</span>
  </div>
  <svg class="pointer" viewBox="0 0 22 28" aria-hidden="true">
    <polygon points="1,1 1,22 6,17 10,27 14,25 10,16 17,16" fill="#111" stroke="#fff" stroke-width="1.2"/>
  </svg>
</main>
</body>
</html>
```